Timber Crest Construction Needs business card

Hey we are in need of business card designs. I have upload our logo as a guideline, but free feel to run with it or come up with something unique.
Pls have fun with it and be creative. the name says it all!
i will give some directions after i see a few entries..
Updates
Logo source file has been uploaded..
Hey because of the logo is so colourful already.
Can we have a few submissions with less colour.
Also we are looking for clever/hidden/descriptive business card.

```html
<!DOCTYPE html>
<html lang="en">
<head>
<meta charset="utf-8">
<title>Timber Crest Construction – Business Card</title>
<link rel="stylesheet" href="https://fonts.googleapis.com/css2?family=Open+Sans:wght@400;600;700&display=swap">
<style>
  :root {
    --backdrop: #e9e6e2;
    --card: #ffffff;
    --ink: #5a5d60;
    --ink-dark: #333333;
    --accent: #5aa9e6;
    --shadow: rgba(0, 0, 0, 0.18);
  }
  * { box-sizing: border-box; margin: 0; padding: 0; }
  html, body { width: 1200px; height: 470px; overflow: hidden; }
  body {
    background: var(--backdrop);
    font-family: "Open Sans", Arial, sans-serif;
    color: var(--ink-dark);
    display: flex;
    align-items: center;
    justify-content: center;
    gap: 40px;
  }
  .card {
    width: 540px;
    height: 320px;
    background: var(--card);
    box-shadow: 0 6px 18px var(--shadow);
    position: relative;
  }

  /* Wordmark */
  .brand {
    font-weight: 700;
    color: var(--ink);
    text-transform: uppercase;
    display: flex;
    align-items: center;
    gap: 10px;
  }
  .brand-mark {
    width: 12px; height: 12px;
    background: var(--ink);
    flex: none;
  }
  .brand-text { display: flex; flex-direction: column; line-height: 1.05; }
  .brand-main { font-size: 24px; letter-spacing: 0.5px; }
  .brand-sub { font-size: 10px; letter-spacing: 1.5px; text-align: right; }

  /* Front */
  .front .brand {
    position: absolute;
    top: 26px; right: 34px;
  }
  .person {
    position: absolute;
    top: 78px; left: 34px;
    font-weight: 700;
    font-size: 18px;
    line-height: 1.2;
  }
  .person-name { color: var(--ink); }
  .person-title { color: var(--accent); }
  .address {
    position: absolute;
    top: 130px; right: 34px;
    text-align: right;
    font-size: 13px;
    line-height: 1.5;
  }
  .contacts {
    position: absolute;
    top: 198px; right: 34px;
    list-style: none;
    font-size: 13px;
    line-height: 1.65;
  }
  .contacts li {
    display: flex;
    align-items: center;
    justify-content: flex-end;
    gap: 5px;
  }
  .contacts svg { width: 12px; height: 12px; flex: none; }
  .icon-fill { fill: var(--ink-dark); }
  .icon-line { fill: none; stroke: var(--ink-dark); stroke-width: 1.1; }

  /* Back */
  .back {
    display: flex;
    align-items: center;
    justify-content: center;
    padding: 40px 60px;
  }
  .back .brand { gap: 14px; }
  .back .brand-mark { width: 18px; height: 18px; }
  .back .brand-main { font-size: 38px; }
  .back .brand-sub { font-size: 15px; letter-spacing: 2px; }
</style>
</head>
<body>
  <section class="card front">
    <div class="brand">
      <span class="brand-mark"></span>
      <span class="brand-text">
        <span class="brand-main">Timber Crest</span>
        <span class="brand-sub">Construction</span>
      </span>
    </div>

    <div class="person">
      <div class="person-name">Your Name</div>
      <div class="person-title">Title</div>
    </div>

    <div class="address">
      Street Name City Name<br>
      State Zipcode
    </div>

    <ul class="contacts">
      <li>
        <svg viewBox="0 0 12 12" aria-hidden="true"><path class="icon-fill" d="M3 1l2 2.5-1.2 1.2a7 7 0 0 0 3.5 3.5L8.5 7 11 9l-1.3 1.8C5.5 11 1 6.5 1.2 2.3z"/></svg>
        0400 555 812
      </li>
      <li>
        <svg viewBox="0 0 12 12" aria-hidden="true"><path class="icon-fill" d="M3 1l2 2.5-1.2 1.2a7 7 0 0 0 3.5 3.5L8.5 7 11 9l-1.3 1.8C5.5 11 1 6.5 1.2 2.3z"/></svg>
        0400 555 812
      </li>
      <li>
        <svg viewBox="0 0 12 12" aria-hidden="true"><path class="icon-line" d="M1 3h10v7H1z M1.5 3.5L6 7l4.5-3.5"/></svg>
        office@timbercrestbuild.com
      </li>
      <li>
        <svg viewBox="0 0 12 12" aria-hidden="true"><g class="icon-line"><circle cx="6" cy="6" r="5"/><ellipse cx="6" cy="6" rx="2.2" ry="5"/><path d="M1 6h10"/></g></svg>
        www.timbercrestbuild.com
      </li>
    </ul>
  </section>

  <section class="card back">
    <div class="brand">
      <span class="brand-mark"></span>
      <span class="brand-text">
        <span class="brand-main">Timber Crest</span>
        <span class="brand-sub">Construction</span>
      </span>
    </div>
  </section>
</body>
</html>
```